RW Holloway LLC Business Card - Civil Engineering & Consulting Firm

We need a Business Card that is elegant, and masculine.  It is our Professional Civil Engineering & Consulting Company located in San Antonio TX (Not s construction or builder firm- no gears & no tool images please). We provide civil engineering services including  commercial site plans, grading and drainage plans, utility plans, hydraulics and hydrology, land planning, utility coordination, and other general civil engineering services related to commercial and residential development.
We have 2 existing Logos. We would like to convey reliability, strength, trustworthiness and attention to detail.  Blues and orange tones as per logo We are OK with the use of a darker blue in the mix.  We have 2 logo versions - Full Company Name Logo to go on the back of card, & Small Icon Logo for the front w/ personal Info.

Target Market(s)
Architects, Real Estate Developers, Other Strctural Engineers, Surveyers, General Contractors
Industry/Entity Type
Professional Civil Engineering
Contact Information for Business Card
Name, Position, Address, Cell & Office #, email, and company website
Font styles to use
Other font styles liked:
- Avian
Requirements
Should not have
- No Tools, No Gears, no Cranes, or Construction Equipment.

```html
<!DOCTYPE html>
<html lang="en">
<head>
<meta charset="utf-8">
<title>RW Holloway LLC Business Card</title>
<link href="https://fonts.googleapis.com/css2?family=Montserrat:wght@400;500;700&display=swap" rel="stylesheet">
<style>
  :root {
    --stage: #1d1d1f;
    --paper: #fafafa;
    --blue: #6fa8d8;
    --orange: #ee8f2a;
    --ink: #1a1a1a;
  }
  * { margin: 0; padding: 0; box-sizing: border-box; }
  html, body { width: 1200px; height: 1015px; overflow: hidden; }
  body {
    background: var(--stage);
    font-family: "Montserrat", sans-serif;
    position: relative;
  }
  .card {
    position: absolute;
    width: 560px;
    height: 320px;
    background: var(--paper);
    overflow: hidden;
  }
  .card-back { left: 80px; top: 120px; }
  .card-front { left: 560px; top: 540px; }

  .brand-lockup {
    position: absolute;
    left: 0; right: 0; top: 0; bottom: 0;
    display: flex;
    align-items: center;
    justify-content: center;
    gap: 14px;
  }
  .brand-mark { width: 34px; height: 34px; background: var(--orange); }
  .brand-name {
    font-size: 38px;
    font-weight: 500;
    color: var(--blue);
    letter-spacing: 2px;
  }

  .corner-tab {
    position: absolute;
    right: 0; top: 34px;
    width: 22px; height: 34px;
    background: var(--orange);
  }
  .person {
    position: absolute;
    right: 36px; top: 36px;
    text-align: right;
  }
  .person-name {
    font-size: 20px;
    font-weight: 700;
    color: var(--orange);
    letter-spacing: 1px;
  }
  .person-role {
    font-size: 13px;
    color: var(--ink);
    margin-top: 4px;
  }
  .divider {
    position: absolute;
    left: 40px; right: 14px; top: 176px;
    height: 2px;
    background: var(--orange);
  }
  .front-brand {
    position: absolute;
    left: 40px; top: 130px;
    font-size: 20px;
    font-weight: 500;
    color: var(--blue);
  }
  .contact-list {
    position: absolute;
    left: 40px; top: 194px;
    list-style: none;
  }
  .contact-list li {
    display: flex;
    align-items: center;
    gap: 12px;
    font-size: 14px;
    color: var(--ink);
    height: 26px;
  }
  .contact-list svg { width: 16px; height: 16px; fill: var(--orange); }
  .address {
    position: absolute;
    right: 36px; top: 200px;
    text-align: right;
    font-size: 14px;
    line-height: 1.5;
    color: var(--ink);
  }
</style>
</head>
<body>
  <section class="card card-back">
    <div class="brand-lockup">
      <span class="brand-mark"></span>
      <span class="brand-name">RW Holloway LLC</span>
    </div>
  </section>

  <section class="card card-front">
    <span class="corner-tab"></span>
    <div class="person">
      <div class="person-name">DALE RENNER</div>
      <div class="person-role">Co-Founder</div>
    </div>
    <div class="front-brand">RW Holloway LLC</div>
    <div class="divider"></div>
    <ul class="contact-list">
      <li><svg viewBox="0 0 24 24"><path d="M6.6 10.8a15 15 0 0 0 6.6 6.6l2.2-2.2c.3-.3.7-.4 1-.2 1.1.4 2.3.6 3.6.6.6 0 1 .4 1 1V20c0 .6-.4 1-1 1A17 17 0 0 1 3 4c0-.6.4-1 1-1h3.5c.6 0 1 .4 1 1 0 1.3.2 2.5.6 3.6.1.3 0 .7-.2 1z"/></svg>555-014-2290</li>
      <li><svg viewBox="0 0 24 24"><rect x="3" y="9" width="18" height="12" rx="2"/><rect x="2" y="3" width="20" height="5" rx="2"/></svg>555-014-3318</li>
      <li><svg viewBox="0 0 24 24"><path d="M2 5h20v14H2z M2 5l10 8 10-8" stroke="#fafafa" stroke-width="1.5"/></svg>info@rwhollowayllc</li>
      <li><svg viewBox="0 0 24 24"><circle cx="12" cy="12" r="10"/></svg>www.hollowayeng.com</li>
    </ul>
    <div class="address">4180 Cedar Bend Road<br>Suite 210 Alder 78</div>
  </section>
</body>
</html>
```